Banner to be displayed at local Farmers Market Booth.

Graphic Design Brief: Farmers Market Banner Contest

Project Overview:We are seeking talented graphic designers to create a visually appealing banner for our booth at the local farmers market. Our company specializes in healthy, all-natural dog and cat treats, and we want a banner that captures our brand identity while drawing in pet owners who value quality and nutrition for their furry friends.

Banner Specifications:

Size: 24 inches x 60 inches (Horizontal orientation) 24" High X 60 wide

Theme: Vintage/Retro

Style: Warm, inviting, nostalgic with a touch of rustic charm

Colors: Earthy, muted tones such as warm browns, soft greens, and creamy yellows. Pops of red or blue may be used sparingly for accents. OR Black and White with gray scales. Would like to see both

Typography: Retro-style fonts that are readable and align with the vintage aesthetic.

Key Elements to Include: website (www.moltbyfarms.com)

Company Name: Moltby Farms

Tagline: " Simply Honest Bites "
Imagery: Illustrations or stylized graphics of happy dogs and cats, possibly interacting with treats.

Emphasis on Natural Ingredients: Icons or design elements that subtly suggest freshness and quality (e.g., leaves, wheat, bones, or paw prints).

Farmers Market Appeal: A design that blends well with the artisanal, handmade, and farm-fresh atmosphere of the market.

Design Considerations:

The banner should be easily readable from a distance.

A balanced composition that doesn't feel overcrowded.

Should evoke trust and warmth while maintaining a professional look.

Avoid overly modern or sleek elements that don’t align with the vintage aesthetic.

Submission Requirements:

High-resolution digital file in PDF or AI format.

CMYK color mode for printing purposes.

Must include a mockup or preview of how it would look in a real farmers market setting.

We look forward to seeing your creative interpretations of our brand! If you have any questions, feel free to reach out.

Font styles to use
Other font styles liked:
• See attachement

Requirements
Nice to have
• Retro/Vintage,playful BUT NOT whimsical

```html
<!DOCTYPE html>
<html lang="en">
<head>
<meta charset="utf-8">
<title>Moltby Farms – Market Banner</title>
<link rel="stylesheet" href="https://fonts.googleapis.com/css2?family=Russo+One&family=Cinzel:wght@500;700;900&display=swap">
<style>
  :root {
    --backdrop: #e3e6ea;
    --ink: #141414;
    --cream: #efebe2;
    --orange: #e8822f;
    --orange-deep: #d2601d;
    --art-light: #cfcfcb;
    --art-dark: #5a5a58;
  }
  html, body {
    margin: 0;
    width: 1200px;
    height: 944px;
    overflow: hidden;
    background: var(--backdrop);
  }
  .banner {
    position: absolute;
    left: 40px;
    top: 252px;
    width: 1120px;
    height: 439px;
    background: var(--orange);
    border-bottom: 8px solid var(--orange-deep);
    box-sizing: border-box;
    overflow: hidden;
  }
  .banner__backdrop {
    position: absolute;
    inset: 0;
    width: 1120px;
    height: 439px;
  }
  .brand-name {
    position: absolute;
    left: 30px;
    top: 36px;
    margin: 0;
    font-family: "Russo One", sans-serif;
    font-weight: 400;
    color: var(--cream);
    font-size: 92px;
    line-height: 90px;
    letter-spacing: 2px;
    text-transform: uppercase;
  }
  .web-address {
    position: absolute;
    left: 30px;
    width: 650px;
    top: 232px;
    text-align: center;
    font-family: "Cinzel", serif;
    font-weight: 500;
    font-size: 25px;
    letter-spacing: 4px;
    color: var(--cream);
    text-transform: uppercase;
  }
  .pet-art {
    position: absolute;
    left: 676px;
    top: 44px;
    width: 436px;
    height: 278px;
    border-radius: 10px;
    background: radial-gradient(ellipse at 45% 45%, var(--art-light) 0%, #9c9c98 55%, var(--art-dark) 100%);
  }
  .market-mark {
    position: absolute;
    right: 24px;
    top: 18px;
    display: flex;
    align-items: center;
    gap: 6px;
    font-family: "Cinzel", serif;
    font-weight: 700;
    font-size: 15px;
    color: var(--cream);
  }
  .market-mark__dot {
    width: 10px;
    height: 10px;
    border-radius: 50%;
    background: var(--cream);
  }
  .tagline {
    position: absolute;
    left: 32px;
    top: 322px;
    margin: 0;
    font-family: "Cinzel", serif;
    font-weight: 900;
    font-size: 42px;
    letter-spacing: 2px;
    color: var(--cream);
    text-shadow: -3px 3px 0 var(--ink);
    text-transform: uppercase;
  }
  .offer {
    position: absolute;
    left: 34px;
    top: 382px;
    margin: 0;
    font-family: "Cinzel", serif;
    font-weight: 500;
    font-size: 29px;
    color: var(--cream);
    text-transform: uppercase;
    white-space: nowrap;
  }
</style>
</head>
<body>
  <section class="banner">
    <svg class="banner__backdrop" viewBox="0 0 1120 439" aria-hidden="true">
      <path fill="var(--ink)" d="M0 0H1120V320L1090 312 1062 322 1030 310 998 318 960 306 930 316 900 304 880 312 860 300H850V318L700 322 690 284 670 292 650 280 620 290 600 276 575 292 555 282 520 300 500 288 470 294 440 284 405 296 380 286 350 294 320 282 290 290 250 278 215 288 185 276 150 290 110 280 80 288 45 278 20 286 0 280Z"/>
    </svg>

    <h1 class="brand-name">Moltby<br>Farms</h1>
    <div class="web-address">www.moltbyfarms.com</div>

    <div class="pet-art" role="img" aria-label="Black and white illustration of a dog and a tabby cat lying side by side"></div>

    <div class="market-mark"><span class="market-mark__dot"></span>Moltby Farms</div>

    <h2 class="tagline">Simply Honest Bites</h2>
    <p class="offer">Purveyors of Premium Pet Food &amp; Treats</p>
  </section>
</body>
</html>
```